Design a New Business Card for Our Company

We are looking for fresh, unique, and a modern business card that reflects our roots as digital marketing agency focused on SEM.

Industry/Entity Type

Marketing

Contact Information for Business Card

looking for very unique out of the box designs. clean and modern that compliments our logo

Requirements
Must have
• colors should match our logo
• Front should have name, address, email, and phone/fax of the person, phone/fax are the same number
• back should have our url

```html
<!DOCTYPE html>
<html lang="en">
<head>
<meta charset="utf-8">
<title>Northpeak Digital – Business Card</title>
<link href="https://fonts.googleapis.com/css2?family=Open+Sans:wght@400;600;700&display=swap" rel="stylesheet">
<style>
  :root {
    --stage: #2b2b2d;
    --card-white: #ffffff;
    --card-grey: #a8a8a8;
    --brand-blue: #4f8fd1;
    --soft-grey: #b9b9b9;
    --text-grey: #8a8a8a;
    --divider: #d6d6d6;
  }
  * { margin: 0; padding: 0; box-sizing: border-box; }
  html, body { width: 1200px; height: 750px; overflow: hidden; }
  body {
    background: var(--stage);
    font-family: "Open Sans", Arial, sans-serif;
    position: relative;
  }
  .card {
    position: absolute;
    top: 225px;
    width: 520px;
    height: 300px;
    border-radius: 22px;
    overflow: hidden;
  }
  /* Back side */
  .card-back { left: 60px; background: var(--card-grey); }
  .back-brand {
    position: absolute;
    right: 36px;
    bottom: 50px;
    display: flex;
    align-items: center;
    gap: 10px;
  }
  .back-brand .brand-dot {
    width: 16px; height: 16px; border-radius: 50%;
    background: var(--brand-blue);
  }
  .back-brand .brand-name {
    color: var(--card-white);
    font-weight: 700;
    font-size: 30px;
    letter-spacing: -0.5px;
  }
  .back-url {
    position: absolute;
    right: 36px;
    bottom: 28px;
    color: var(--card-white);
    font-size: 12px;
    font-weight: 600;
  }

  /* Front side */
  .card-front { left: 620px; background: var(--card-white); }
  .front-brand {
    position: absolute;
    left: 32px;
    top: 150px;
    display: flex;
    align-items: center;
    gap: 8px;
  }
  .front-brand .brand-dot {
    width: 13px; height: 13px; border-radius: 50%;
    background: var(--soft-grey);
  }
  .front-brand .brand-name {
    color: var(--brand-blue);
    font-weight: 700;
    font-size: 22px;
    letter-spacing: -0.4px;
  }
  .divider {
    position: absolute;
    left: 250px;
    top: 40px;
    width: 1px;
    height: 160px;
    background: var(--divider);
  }
  .contact-block {
    position: absolute;
    left: 268px;
    top: 36px;
    color: var(--text-grey);
    font-size: 12px;
    line-height: 1.35;
  }
  .person-name { color: var(--brand-blue); font-weight: 700; font-size: 15px; }
  .person-role { font-size: 11px; margin-bottom: 10px; }
  .address { margin-bottom: 10px; }
  .contact-row { display: flex; align-items: center; gap: 6px; height: 17px; }
  .contact-icon { width: 13px; height: 13px; flex: none; }
  .card-wave { position: absolute; left: 0; top: 0; }
</style>
</head>
<body>

<section class="card card-back" aria-label="Business card back">
  <div class="back-brand">
    <span class="brand-dot"></span>
    <span class="brand-name">Northpeak Digital</span>
  </div>
  <p class="back-url">www.northpeakdigital.com</p>
</section>

<section class="card card-front" aria-label="Business card front">
  <svg class="card-wave" width="520" height="300" viewBox="0 0 520 300" aria-hidden="true">
    <path d="M200,300 C320,282 420,228 520,192 L520,300 Z" fill="var(--soft-grey)"/>
    <path d="M0,282 C160,300 330,255 430,200 C465,182 495,172 520,168 L520,177 C492,184 462,196 432,213 C330,272 160,306 0,293 Z" fill="var(--brand-blue)"/>
  </svg>

  <div class="front-brand">
    <span class="brand-dot"></span>
    <span class="brand-name">Northpeak Digital</span>
  </div>

  <div class="divider"></div>

  <div class="contact-block">
    <p class="person-name">Evan Carter</p>
    <p class="person-role">Owner</p>
    <p class="address">N. 24 Alder Road, Suite 200,<br>Tacoma, WA 98400</p>

    <div class="contact-row">
      <svg class="contact-icon" viewBox="0 0 13 13" aria-label="Phone"><rect width="13" height="13" rx="2" fill="var(--brand-blue)"/><path d="M4 3 L5.5 3 L6 5 L5 5.8 C5.5 7 6.2 7.6 7.2 8 L8 7 L10 7.5 L10 9 C6.5 9.5 3.5 6.5 4 3 Z" fill="#fff"/></svg>
      <span>555.014.2208</span>
    </div>
    <div class="contact-row">
      <svg class="contact-icon" viewBox="0 0 13 13" aria-label="Fax"><rect width="13" height="13" rx="2" fill="var(--brand-blue)"/><rect x="4" y="2.5" width="5" height="3" fill="#fff"/><rect x="2.5" y="5.5" width="8" height="3.5" fill="#fff"/><rect x="4" y="9" width="5" height="1.8" fill="#fff"/></svg>
      <span>555.014.2208</span>
    </div>
    <div class="contact-row">
      <svg class="contact-icon" viewBox="0 0 13 13" aria-label="Email"><rect width="13" height="13" rx="2" fill="var(--brand-blue)"/><rect x="2.5" y="3.8" width="8" height="5.4" fill="none" stroke="#fff" stroke-width="1"/><path d="M2.5 3.8 L6.5 7 L10.5 3.8" fill="none" stroke="#fff" stroke-width="1"/></svg>
      <span>hello@northpeakdigital.com</span>
    </div>
    <div class="contact-row">
      <svg class="contact-icon" viewBox="0 0 13 13" aria-label="Website"><rect width="13" height="13" rx="2" fill="var(--brand-blue)"/><circle cx="6.5" cy="6.5" r="3.8" fill="none" stroke="#fff" stroke-width="1"/><path d="M2.7 6.5 H10.3 M6.5 2.7 C4.8 5 4.8 8 6.5 10.3 M6.5 2.7 C8.2 5 8.2 8 6.5 10.3" fill="none" stroke="#fff" stroke-width="0.8"/></svg>
      <span>www.northpeakdigital.com</span>
    </div>
  </div>
</section>

</body>
</html>
```